Digital Book Cover

I am currently in the process of building a digital book for my web site but struggling with the front and back covers. We are an ecommerce business selling notice boards of all kind, indoor, outdoor, hospitality, staff boards, whiteboards, mobile and so on.

The company web site is orange and white. We already have a company logo which we would like included. The logo is simply the word "larchwick" in black and the work "company" in orange. When our web site was redesigned the company that designed it reversed the colours of the logo and had the word "larchwick" in black & "company" in white onto an orange banner. Either way I don't mind.

Target Market(s)

We sell to everyone online including schools colleges, universities, KTB, companies, churches, supermarkets, hotels etc. If fact everyone!

Industry/Entity Type

Digital

Requirements
Must have
• Company colours and include the company logo and strap line "A Notice Board For Every Location"
• Company details including postal address, phone, fax, email and web site.
• Finish cover to be supplied as a PDF

```html
<!DOCTYPE html>
<html lang="en">
<head>
<meta charset="utf-8">
<title>Larchwick Company – Back Cover</title>
<link href="https://fonts.googleapis.com/css2?family=Arimo:wght@400&display=swap" rel="stylesheet">
<style>
  :root {
    --orange-top: #e6a415;
    --orange-bottom: #fbb51f;
    --ring-white: #ffffff;
    --inner-light: #f6d89b;
    --inner-warm: #f7c257;
    --ink: #1e1e1e;
  }
  html, body {
    margin: 0;
    padding: 0;
    overflow: hidden;
    background: #ffffff;
  }
  .back-cover {
    position: relative;
    width: 848px;
    height: 1200px;
    overflow: hidden;
    background: linear-gradient(180deg, var(--orange-top) 0%, var(--orange-bottom) 100%);
    font-family: "Arimo", Arial, sans-serif;
    color: var(--ink);
  }
  .ring-decoration {
    position: absolute;
    inset: 0;
  }
  .contact-line {
    position: absolute;
    left: 56px;
    margin: 0;
    line-height: 1;
    white-space: nowrap;
    font-weight: 400;
  }
  .company-name { top: 919px; font-size: 29px; }
  .address-house { top: 963px; font-size: 34px; }
  .address-town  { top: 1011px; font-size: 24px; }
  .phone-fax     { top: 1069px; font-size: 20.5px; }
  .email         { top: 1104px; font-size: 21.5px; }
  .website       { top: 1136px; font-size: 25px; }
</style>
</head>
<body>
  <main class="back-cover">
    <svg class="ring-decoration" width="848" height="1200" viewBox="0 0 848 1200" aria-hidden="true">
      <defs>
        <linearGradient id="innerFill" x1="0" y1="0" x2="0" y2="1">
          <stop offset="0" stop-color="var(--inner-light)"/>
          <stop offset="1" stop-color="var(--inner-warm)"/>
        </linearGradient>
      </defs>
      <circle cx="1196" cy="544" r="530" fill="var(--ring-white)"/>
      <circle cx="1196" cy="548" r="428" fill="url(#innerFill)"/>
    </svg>

    <address class="contact-details" style="font-style: normal;">
      <p class="contact-line company-name">Larchwick Company (UK) Ltd</p>
      <p class="contact-line address-house">Harrow House - PO Box 4173</p>
      <p class="contact-line address-town">Ashbury - West Midlands - AB4 2KT</p>
      <p class="contact-line phone-fax">Phone: 01632 960418 - Fax: 01632 960527</p>
      <p class="contact-line email">Email: sales@larchwickcompany.com</p>
      <p class="contact-line website">Web: www.larchwickcompany.com</p>
    </address>
  </main>
</body>
</html>
```